Mortgage Company ready to make a statement!

We have a basic logo that I am fairly happy with ... but it could use a little bit of tweaking before we order the sign for our building. We also want some knock-your-socks-off business cards.
Problem: Inside of our Mortgage Office (Bright Fern Mortgage Group), we are going to have a coffee lounge (Sunbrew Cafe) for Realtors to use instead of the local Cuppington to meet with homebuyers. The office and coffee lounge are in an industrial building and is decorated with cozy overstuffed chairs, a hodge podge of interesting lamps and furniture, and goal is to make it as inviting as possible. However, we are a financial institution... so we need to keep it pretty clean as well.
One of my favorite marketing ideas is to cut a house key for everyone who buys a home using us with a key that matches our logo. There's only one key shape that works really well, so that needs to match the logo in order for the idea to work. I'll attach an image of the key blank.... although the way the key hole cut out looks terrible, so I was thinking of having them just do a thin outline instead.
Would like a similar, matching logo for the Sunbrew Cafe... but possibly something that would be a little less formal and would be cute on a coffee mug- nothing stuffy.
AND, we're opening a home inspection company as well, and we would like that logo and branding to match. The home inspection company is "Bright Fern Home Inspections"
We were thinking that for the home inspection company , we could use a magnifying glass shape inside of the house shape for the logo, use a keyhole shape inside of the same house for the mortgage company, and use a coffee cup inside of the house shape for Sunbrew Cafe.
Just getting stuck and need to help. I designed the attached logo myself, and that is what we are currently using. Designers at local printing companies have failed to impress us.
The mortgage industry has a lot of numbers and logos, etc that they require us to put on our business cards... so it's hard to keep them looking clean.
HELP! HELP! :)

```html
<!DOCTYPE html>
<html lang="en">
<head>
<meta charset="utf-8">
<title>Bright Fern Mortgage Group – Business Cards</title>
<link rel="stylesheet" href="https://fonts.googleapis.com/css2?family=Marcellus&family=Montserrat:wght@400;600&display=swap">
<style>
  :root {
    --backdrop: #ecebe6;
    --card: #ffffff;
    --brand-blue: #1f5f86;
    --ink: #3a3a3c;
    --rule: #2b5573;
    --shadow: rgba(0, 0, 0, 0.28);
  }
  * { box-sizing: border-box; margin: 0; padding: 0; }
  html, body {
    width: 1200px;
    height: 929px;
    overflow: hidden;
    background: var(--backdrop);
  }
  .stage {
    position: relative;
    width: 1200px;
    height: 929px;
  }
  .card {
    position: absolute;
    width: 540px;
    height: 309px;
    background: var(--card);
    box-shadow: 2px 4px 8px var(--shadow);
  }
  .card--front { left: 60px; top: 150px; }
  .card--back  { left: 600px; top: 470px; }

  .wordmark {
    display: flex;
    align-items: center;
    gap: 12px;
    font-family: "Marcellus", serif;
    color: var(--brand-blue);
    letter-spacing: 0.02em;
  }
  .wordmark__square {
    width: 18px;
    height: 18px;
    background: var(--brand-blue);
  }
  .card--front .wordmark {
    position: absolute;
    left: 0; right: 0; top: 128px;
    justify-content: center;
    font-size: 30px;
  }
  .card--back .wordmark {
    position: absolute;
    left: 0; right: 0; top: 62px;
    justify-content: center;
    font-size: 26px;
  }

  .person {
    position: absolute;
    left: 58px;
    top: 160px;
    width: 200px;
    text-align: right;
  }
  .person__name {
    font-family: "Marcellus", serif;
    font-size: 22px;
    color: var(--brand-blue);
    letter-spacing: 0.04em;
  }
  .person__title {
    font-family: "Montserrat", sans-serif;
    font-weight: 600;
    font-size: 14px;
    color: var(--ink);
    margin-top: 2px;
  }
  .divider {
    position: absolute;
    left: 276px;
    top: 150px;
    width: 1.5px;
    height: 64px;
    background: var(--rule);
  }
  .contacts {
    position: absolute;
    left: 292px;
    top: 148px;
    list-style: none;
    font-family: "Montserrat", sans-serif;
    font-size: 13px;
    color: var(--ink);
  }
  .contacts li {
    display: flex;
    align-items: center;
    gap: 8px;
    height: 22px;
  }
  .contacts svg { width: 12px; height: 12px; flex: none; }
  .address {
    position: absolute;
    left: 0; right: 0; bottom: 36px;
    text-align: center;
    font-family: "Montserrat", sans-serif;
    font-size: 13px;
    letter-spacing: 0.05em;
    color: var(--ink);
  }
</style>
</head>
<body>
<main class="stage">
  <section class="card card--front" aria-label="Business card front">
    <div class="wordmark"><span class="wordmark__square"></span>Bright Fern Mortgage Group</div>
  </section>

  <section class="card card--back" aria-label="Business card back">
    <div class="wordmark"><span class="wordmark__square"></span>Bright Fern Mortgage Group</div>

    <div class="person">
      <p class="person__name">ALAN MARSH</p>
      <p class="person__title">CEO</p>
    </div>
    <div class="divider"></div>
    <ul class="contacts">
      <li>
        <svg viewBox="0 0 12 12" aria-hidden="true"><rect x="3" y="0.5" width="6" height="11" rx="1" fill="none" stroke="#1f5f86" stroke-width="1.2"/></svg>
        000-123-4567
      </li>
      <li>
        <svg viewBox="0 0 12 12" aria-hidden="true"><rect x="3" y="0.5" width="6" height="3" fill="#1f5f86"/><rect x="0.5" y="4" width="11" height="5" rx="1" fill="#1f5f86"/><rect x="3" y="8" width="6" height="3.5" fill="#fff" stroke="#1f5f86"/></svg>
        000-123-4567
      </li>
      <li>
        <svg viewBox="0 0 12 12" aria-hidden="true"><rect x="0.5" y="2" width="11" height="8" fill="#1f5f86"/><path d="M0.5 2 L6 6.5 L11.5 2" fill="none" stroke="#fff" stroke-width="1"/></svg>
        alan.marsh@brightfernmg.com
      </li>
    </ul>
    <p class="address">Lantern Court Sydney Melbourne</p>
  </section>
</main>
</body>
</html>
```